Web Design Project

i'm looking for a sleek modern design i can use for a web site that deals with.
Intelligent Data Capture
Accounts Payable Solutions for faster processing based on our scanning solution.
ultimately we are a intelligent scanning software.

here is a great website, that does exactly what we do, and we like to have most of their services and products.

so something in this idea would be great.
www.valtrino.com

so i guess i want a good landing/home page which is smartly designed so users will be inclined to leave their information.

and then information pages.

also i dont need any cms for you to include, i only need you to hook the html hooks for RANK Kettle as i already have a CMS and need it to hook in to that, i am including links to that cheat sheet.
so it is easier when included as you create the Theme.

http://www.rankkettle.com/how-to-create-website-template.html
http://www.rankkettle.com/cheat-sheet.html
Updates

Hi Guys sorry for the long pause in design, but here is where we stand.

what ever design i choose, i need that designer to customize a few things for me based on design that was designed.
and i will need designer to match that them to work with RANK Kettle
here is the cheat sheet for the hooks that we need to match and make it work.
if you have any questions let me know.

otherwise i look forward to working with you. and good luck.

Target Market(s)

CFO's AP Managers, mostly ppl who are not Tech freindly

Industry/Entity Type

Software

Requirements
Must have
• i need on home page, the rotating banner should have 1 ability to place youtube links to show videos, and also ability to add buttons on these rotating banners that will allow forms to pop up take to another page.

```html
<!DOCTYPE html>
<html lang="en">
<head>
<meta charset="utf-8">
<title>KORVA – Intelligent Data Capture</title>
<link href="https://fonts.googleapis.com/css2?family=Arimo:wght@400;700&display=swap" rel="stylesheet">
<style>
:root{
  --blue-dark:#0d4f86;
  --blue:#2a76b8;
  --blue-light:#4f98d2;
  --link:#2a7fc4;
  --heading:#1f6ba8;
  --text:#6a6a6a;
  --nav-bg:#2f2f2f;
  --nav-active:#2c5d94;
  --grey-bg:#c7c7c7;
  --box-bg:#f6f6f6;
  --footer:#3c3c3c;
  --footer-text:#d8d8d8;
}
*{margin:0;padding:0;box-sizing:border-box}
html,body{width:1200px;height:1169px;overflow:hidden}
body{font-family:"Arimo",Arial,sans-serif;background:linear-gradient(#c4c4c4 157px,#dcdcdc 500px,#fff 880px);position:relative;color:var(--text)}
.site-header{position:absolute;left:0;top:0;width:1200px;height:157px;background:linear-gradient(#3d86c6,#1c63a4 60%,#0e4f8c);border-bottom:2px solid #e6e6e6}
.logo{position:absolute;left:88px;top:18px;font-size:54px;font-weight:700;color:#fff;letter-spacing:1px}
.search{position:absolute;left:892px;top:31px;width:220px;height:33px;border-radius:17px;background:#fff;border:1px solid #c9d6e2;font-size:12px;font-style:italic;color:#a0a0a0;padding:10px 17px}
.search svg{position:absolute;right:16px;top:11px}
.page{position:absolute;left:89px;top:99px;width:1024px;height:987px;background:#fff}
.main-nav{position:absolute;left:4px;top:4px;display:flex;height:51px;width:1015px;background:linear-gradient(#474747,#262626)}
.main-nav a{display:flex;align-items:center;justify-content:center;color:#fff;text-decoration:none;font-size:14.5px;border-right:1px solid #1c1c1c}
.main-nav a.active{background:linear-gradient(#3a6ea8,#254f82)}
.main-nav a.account{background:linear-gradient(#333,#1b1b1b)}
.hero{position:absolute;left:4px;top:61px;width:1015px;height:301px;background:#3c3c3c;padding:4px}
.hero-inner{position:relative;width:100%;height:100%;background:linear-gradient(90deg,#5d6d7c,#7b8a98 55%,#a9b6c2);overflow:hidden}
.hero-photo{position:absolute;right:0;top:0;width:440px;height:100%;background:linear-gradient(90deg,rgba(160,175,190,0),#c5d0da 45%,#8a97a3)}
.hero h1{position:absolute;left:48px;top:64px;width:420px;font-weight:400;font-size:31px;line-height:42px;color:#fff}
.hero p{position:absolute;left:48px;top:150px;width:380px;font-size:12.5px;line-height:21px;color:#fff}
.dots{position:absolute;left:28px;top:250px;display:flex;gap:10px}
.dots span{width:12px;height:12px;border-radius:50%;background:#fff}
.dots span.on{background:#5aaef0;box-shadow:0 0 0 2px #cfe6fa}
.welcome{position:absolute;left:12px;top:393px;width:344px}
h2{font-weight:400;color:var(--heading)}
.welcome h2{font-size:27px}
.copy{font-size:12.5px;line-height:21px;text-align:justify;margin-top:12px}
.video{position:absolute;left:1px;top:131px;width:342px;height:184px;border:4px solid #c2c2c2;background:linear-gradient(135deg,#a9b3bd,#d9dee3 50%,#6f7881)}
.play{position:absolute;left:137px;top:67px;width:60px;height:40px;border-radius:8px;background:#111}
.play::after{content:"";position:absolute;left:24px;top:11px;border-left:16px solid #fff;border-top:9px solid transparent;border-bottom:9px solid transparent}
.divider-v{position:absolute;left:390px;top:397px;width:1px;height:315px;background:#cfcfcf}
.service{position:absolute;left:425px;top:393px;width:588px}
.service h2{font-size:21px}
.service .copy{width:450px}
.service-icon{position:absolute;right:0;top:45px;width:114px;height:84px;background:radial-gradient(circle at 35% 45%,#3c87d6,#9cc3e6 45%,#eef2f5 70%);border-radius:6px}
.divider-h{position:absolute;left:425px;top:552px;width:589px;height:1px;background:#bdbdbd}
.solutions{position:absolute;left:425px;top:571px;width:589px}
.solutions h2{font-size:21px}
.sol-list{list-style:none;display:grid;grid-template-columns:293px 296px;row-gap:16px;margin-top:17px}
.sol-list li{position:relative;padding-left:23px;font-size:13px;line-height:19px;color:var(--link);width:235px}
.sol-list li:nth-child(even){width:296px}
.sol-list li svg{position:absolute;left:0;top:4px}
.divider-full{position:absolute;left:11px;top:750px;width:1002px;height:1px;background:#bdbdbd}
.feed{position:absolute;top:766px;width:328px}
.feed-head{height:47px;background:linear-gradient(#4aa1d6,#2a81bc 55%,#1f72ad);position:relative;color:#fff;font-size:21px;padding:11px 0 0 83px}
.feed-icon{position:absolute;left:14px;top:3px;width:54px;height:42px;background:linear-gradient(#fff,#cfd6dc);border-radius:4px;transform:rotate(-12deg)}
.feed-icon.plain{width:38px;height:38px;border-radius:50%;background:#e8eef3;transform:none;left:16px;top:4px}
.feed-body{background:var(--box-bg);height:106px;padding:14px 0 0 22px;position:relative}
.feed-body h3{font-weight:400;font-size:15.5px;color:var(--heading);padding-left:20px;position:relative}
.feed-body h3::before{content:"";position:absolute;left:0;top:5px;border-left:4px solid var(--heading);border-top:4px solid transparent;border-bottom:4px solid transparent}
.feed-body p{font-size:12px;line-height:17px;padding-left:20px;margin-top:5px;letter-spacing:.3px}
.feed-body time{display:block;padding-left:20px;font-size:12px;color:#222;margin-top:8px;letter-spacing:.3px}
.feed-more{background:var(--box-bg);height:40px;margin-top:4px;text-align:right;padding:12px 20px 0 0;font-size:14px;color:var(--heading)}
.feed-more::after{content:"";display:inline-block;margin-left:6px;border-left:4px solid var(--heading);border-top:4px solid transparent;border-bottom:4px solid transparent;vertical-align:1px}
.site-footer{position:absolute;left:0;top:1086px;width:1200px;height:83px;background:var(--footer)}
.foot-nav{position:absolute;left:90px;top:20px;font-size:13px;color:var(--footer-text)}
.foot-nav a{color:var(--footer-text);text-decoration:none}
.foot-nav .sep{margin:0 9px}
.copyright{position:absolute;left:90px;top:51px;font-size:12.5px;color:var(--footer-text)}
.social{position:absolute;left:1051px;top:29px;display:flex;gap:12px}
.social span{width:25px;height:25px;border-radius:50%;background:#8a8a8a}
</style>
</head>
<body>
<header class="site-header">
  <div class="logo">KORVA</div>
  <div class="search">Search
    <svg width="12" height="12" viewBox="0 0 12 12"><circle cx="4.5" cy="4.5" r="3.3" fill="none" stroke="#999" stroke-width="1.4"/><line x1="7" y1="7" x2="11" y2="11" stroke="#999" stroke-width="1.6"/></svg>
  </div>
</header>

<main class="page">
  <nav class="main-nav">
    <a class="active" style="width:93px">Home</a>
    <a style="width:88px">About</a>
    <a style="width:106px">Solutions</a>
    <a style="width:106px">Products</a>
    <a style="width:147px">News &amp; Events</a>
    <a style="width:79px">Blog</a>
    <a style="width:98px">Support</a>
    <a style="width:98px">Contact</a>
    <a class="account" style="width:85px">Login</a>
    <a class="account" style="width:115px;border-right:0">Register</a>
  </nav>

  <section class="hero">
    <div class="hero-inner">
      <div class="hero-photo" role="img" aria-label="Businessman touching a glowing network of user profiles"></div>
      <h1>Intelligent data capture from online sites</h1>
      <p>Nam tempus nisl nec massa gravida facilisis. Vestibulum rhoncus auctor lorem, luctus pretium magna aliquam eget.</p>
      <div class="dots"><span class="on"></span><span></span><span></span><span></span></div>
    </div>
  </section>

  <section class="welcome">
    <h2>Welcome to our site</h2>
    <p class="copy">Donec in turpis mi, eget imperdiet lacus. In vitae mauris et nulla commodo iaculis facilisis quis odio. Aliquam ornare sodales nisl, eu ultrices arcu consequat ut. Praesent pulvinar commodo quam a cursus adipiscing.</p>
    <div class="video" role="img" aria-label="Video still of a hand on a computer mouse at a desk"><span class="play"></span></div>
  </section>

  <div class="divider-v"></div>

  <section class="service">
    <h2>About Our Service</h2>
    <p class="copy">Cras augue eros, lobortis rhoncus accumsan iaculis, suscipit lobortis neque. In id nisl nec odio porttitor fermentum. Phasellus sagittis malesuada magna, a semper ipsum ultrices a. Suspendisse auctor vestibulum commodo. Donec id ornare est. Fusce aliquet sapien sit amet eros cursus eget sollicitudin nulla gravida. In ac leo id nisi placerat euismod.</p>
    <div class="service-icon" role="img" aria-label="Globe, computer monitor and document illustration"></div>
  </section>

  <div class="divider-h"></div>

  <section class="solutions">
    <h2>Solutions</h2>
    <ul class="sol-list">
      <li><svg width="13" height="10" viewBox="0 0 13 10"><path d="M0 3h7V0l6 5-6 5V7H0z" fill="#8fb9dc"/></svg>Electronic Document Management Systems</li>
      <li><svg width="13" height="10" viewBox="0 0 13 10"><path d="M0 3h7V0l6 5-6 5V7H0z" fill="#8fb9dc"/></svg>Document &amp; information Capture Services</li>
      <li><svg width="13" height="10" viewBox="0 0 13 10"><path d="M0 3h7V0l6 5-6 5V7H0z" fill="#8fb9dc"/></svg>Industry Specific Electronic Document Management Solutions</li>
      <li><svg width="13" height="10" viewBox="0 0 13 10"><path d="M0 3h7V0l6 5-6 5V7H0z" fill="#8fb9dc"/></svg>On-line Back-up &amp; Disaster Recovery</li>
    </ul>
  </section>

  <div class="divider-full"></div>

  <article class="feed" style="left:11px">
    <div class="feed-head"><span class="feed-icon" role="img" aria-label="Folded newspaper"></span>Latest News</div>
    <div class="feed-body"><h3>Mauris commodo feugiat</h3><p>Nulla facilisi. Curabitur at elit ligula,<br>eget hendrerit felis vehicula.</p><time>Dec-26-2012</time></div>
    <div class="feed-more">View All</div>
  </article>
  <article class="feed" style="left:349px">
    <div class="feed-head"><span class="feed-icon" role="img" aria-label="Desk calendar"></span>Latest Events</div>
    <div class="feed-body"><h3>Mauris commodo feugiat</h3><p>Nulla facilisi. Curabitur at elit ligula,<br>eget hendrerit felis vehicula.</p><time>Dec-26-2012</time></div>
    <div class="feed-more">View All</div>
  </article>
  <article class="feed" style="left:686px">
    <div class="feed-head"><span class="feed-icon plain"></span>Latest Blog</div>
    <div class="feed-body"><h3>Mauris commodo feugiat</h3><p>Nulla facilisi. Curabitur at elit ligula,<br>eget hendrerit felis vehicula.</p><time>Dec-26-2012</time></div>
    <div class="feed-more">View All</div>
  </article>
</main>

<footer class="site-footer">
  <nav class="foot-nav">
    <a>Home</a><span class="sep">|</span><a>About</a><span class="sep">|</span><a>Solutions</a><span class="sep">|</span><a>Products</a><span class="sep">|</span><a>News &amp; Events</a><span class="sep">|</span><a>Blog</a><span class="sep">|</span><a>Support</a><span class="sep">|</span><a>Contact</a><span class="sep">|</span><a>Login</a><span class="sep">|</span><a>Register</a>
  </nav>
  <p class="copyright">Copyright &nbsp;©&nbsp; 2013 &nbsp; www.korva.com &nbsp; All rights reserved.</p>
  <div class="social"><span></span><span></span></div>
</footer>
</body>
</html>
```